TA BRAMLEY BUSINESS CARD DESIGN PROJECT

We need to utilize our logo that was expertly created on PixelHarbor and now need to match this with a business card design.

```html
<!DOCTYPE html>
<html lang="en">
<head>
<meta charset="utf-8">
<title>TA Bramley Business Card</title>
<link rel="stylesheet" href="https://fonts.googleapis.com/css2?family=Montserrat:wght@400;500;700;800&display=swap">
<style>
  :root {
    --stage: #ecebe8;
    --paper: #ffffff;
    --brand-blue: #1155b0;
    --ink: #2a2a2a;
    --back-dark: #161616;
    --back-mid: #262626;
  }
  * { margin: 0; padding: 0; box-sizing: border-box; }
  html, body { width: 1200px; height: 834px; overflow: hidden; }
  body {
    background: var(--stage);
    font-family: "Montserrat", sans-serif;
    display: flex;
    align-items: center;
    justify-content: center;
    gap: 40px;
  }
  .card {
    width: 540px;
    height: 310px;
    border-radius: 6px;
    position: relative;
    overflow: hidden;
    box-shadow: 0 10px 28px rgba(0,0,0,.18);
  }
  .card-front { background: var(--paper); }
  .front-wave { position: absolute; inset: 0; width: 100%; height: 100%; }

  .brand-name {
    position: absolute;
    left: 36px;
    top: 98px;
    width: 200px;
    display: flex;
    align-items: center;
    gap: 10px;
    color: var(--brand-blue);
    font-weight: 800;
    font-size: 22px;
    letter-spacing: 1px;
  }
  .brand-square {
    width: 18px; height: 18px;
    background: var(--brand-blue);
    flex: none;
  }
  .divider {
    position: absolute;
    left: 252px;
    top: 52px;
    width: 1.5px;
    height: 166px;
    background: var(--brand-blue);
  }
  .contact {
    position: absolute;
    left: 274px;
    top: 50px;
    color: var(--ink);
  }
  .person-name {
    color: var(--brand-blue);
    font-weight: 800;
    font-size: 20px;
    letter-spacing: .5px;
  }
  .person-title {
    font-size: 13px;
    font-weight: 500;
    margin: 2px 0 12px;
  }
  .contact-list { list-style: none; font-size: 13px; line-height: 18px; }
  .contact-list li { display: flex; align-items: center; gap: 7px; }
  .contact-list svg { width: 11px; height: 11px; fill: var(--brand-blue); flex: none; }
  .address { font-size: 13px; line-height: 18px; margin-top: 4px; }

  .card-back {
    border-radius: 22px;
    background: linear-gradient(135deg, var(--back-mid), var(--back-dark) 60%);
  }
</style>
</head>
<body>
  <article class="card card-front">
    <svg class="front-wave" viewBox="0 0 540 310" preserveAspectRatio="none" aria-hidden="true">
      <path d="M0 300 C70 300 130 170 220 200 C320 232 430 300 540 270 L540 310 L0 310 Z" fill="var(--brand-blue)"/>
      <path d="M0 292 C70 292 130 160 220 190 C320 222 430 292 540 262" fill="none" stroke="var(--brand-blue)" stroke-width="1.5"/>
    </svg>

    <div class="brand-name"><span class="brand-square"></span>TA BRAMLEY</div>
    <div class="divider"></div>

    <div class="contact">
      <h1 class="person-name">MARCUS HALE</h1>
      <p class="person-title">Managing Director</p>
      <ul class="contact-list">
        <li><svg viewBox="0 0 12 12"><path d="M2 1h2.5l1 3-1.5 1a6 6 0 0 0 3 3l1-1.5 3 1V10a1 1 0 0 1-1 1A9 9 0 0 1 1 2a1 1 0 0 1 1-1z"/></svg>123 456 789</li>
        <li><svg viewBox="0 0 12 12"><rect x="3" y="0.5" width="6" height="11" rx="1"/></svg>123 456 789</li>
        <li><svg viewBox="0 0 12 12"><path d="M0 2h12v8H0z M0 2l6 5 6-5" /></svg>info@yourgmail.com</li>
        <li><svg viewBox="0 0 12 12"><circle cx="6" cy="6" r="5.5"/></svg>www.yourwebsite.com</li>
      </ul>
      <p class="address">Your address, City<br>State, Zip 1234</p>
    </div>
  </article>

  <article class="card card-back" role="img" aria-label="Dark card back with a tonal repeating brand pattern"></article>
</body>
</html>
```